Jolly Paws Business Card Update

I have a business card which I love. I want to keep the same logo, colours, font and style. I want to upgrade the scripting and remove some elements and add others.
On the front side under Services - remove the existing wording and insert - Providing individual coaching strategies to create happy, healthy and social canine companions
Under Denise Carvell amend the current wording to read: Qualified in Dog Behavioural Training, Natural Animal Healthcare and Animal Health Science
On the reverse side to remove the web address.

```html
<!DOCTYPE html>
<html lang="en">
<head>
<meta charset="utf-8">
<title>Jolly Paws Business Card</title>
<link href="https://fonts.googleapis.com/css2?family=Open+Sans:wght@300;400;600;700&family=Noto+Sans:wght@400;600&family=Arimo:wght@400;700&display=swap" rel="stylesheet">
<style>
  :root {
    --bg: #2a2a2a;
    --blue-deep: #1f3f97;
    --blue-bright: #0a8fd0;
    --navy: #2b2f86;
    --red-dark: #5a1a1c;
    --red-bright: #c8161d;
    --card-light: #efefef;
    --cream: #e9e2c8;
    --white: #ffffff;
    --ink: #111111;
  }
  * { margin: 0; padding: 0; box-sizing: border-box; }
  html, body { width: 1200px; height: 1138px; overflow: hidden; }
  body { background: var(--bg); position: relative; font-family: "Open Sans", sans-serif; }

  .card {
    position: absolute;
    border-radius: 14px;
    overflow: hidden;
    box-shadow: 0 6px 14px rgba(0,0,0,0.45);
  }

  /* Front */
  .card-front {
    left: 274px; top: 186px; width: 623px; height: 376px;
    background: linear-gradient(160deg, var(--blue-deep) 0%, #1565b8 55%, var(--blue-bright) 100%);
  }
  .front-mark {
    position: absolute; left: 236px; top: 35px; width: 150px; height: 150px;
    border-radius: 50%; background: var(--cream);
  }
  .brand-name {
    position: absolute; left: 0; right: 0; top: 191px;
    text-align: center; color: var(--white);
    font-family: "Open Sans", sans-serif; font-weight: 600; font-size: 36px; letter-spacing: 1px;
  }
  .brand-tagline {
    position: absolute; left: 0; right: 0; top: 236px;
    text-align: center; color: var(--white);
    font-weight: 400; font-size: 20px; letter-spacing: 0.3px;
  }
  .front-band {
    position: absolute; left: 0; right: 0; top: 302px; bottom: 0;
    background: linear-gradient(90deg, var(--red-dark) 0%, var(--red-bright) 50%, var(--red-dark) 100%);
  }
  .services-pill {
    position: absolute; left: 218px; top: 287px; width: 186px; height: 29px;
    border-radius: 15px; background: linear-gradient(#ffffff, #dcdcdc);
    border: 2px solid #1c4e9c;
    color: #1b2140; font-weight: 700; font-size: 18px; letter-spacing: 3px;
    text-align: center; line-height: 25px;
  }
  .front-services-text {
    position: absolute; left: 0; right: 0; top: 320px;
    text-align: center; color: #f1d4d4; font-size: 16.5px; line-height: 22px;
  }

  /* Back */
  .card-back {
    left: 276px; top: 608px; width: 618px; height: 374px;
    background: var(--card-light);
    font-family: "Noto Sans", sans-serif;
  }
  .person-name {
    position: absolute; left: 22px; top: 36px;
    color: var(--navy); font-weight: 600; font-size: 26px;
  }
  .person-quals {
    position: absolute; left: 22px; top: 70px;
    color: var(--navy); font-size: 14.5px; line-height: 20px;
  }
  .contact-band {
    position: absolute; left: 0; right: 0; top: 135px; height: 67px;
    background: linear-gradient(90deg, var(--red-dark) 0%, var(--red-bright) 55%, var(--red-dark) 100%);
  }
  .contact-row {
    position: absolute; left: 22px; display: flex; align-items: center; gap: 10px;
    color: var(--white); font-size: 16px;
  }
  .contact-row svg { width: 14px; height: 14px; fill: var(--white); }
  .contact-row .spacer { width: 6px; }
  .row-1 { top: 10px; }
  .row-2 { top: 33px; }
  .services-band {
    position: absolute; left: 0; right: 0; top: 202px; height: 102px;
    background: linear-gradient(90deg, #283c8c 0%, #1c5fb0 55%, var(--blue-bright) 100%);
    font-family: "Arimo", sans-serif; color: var(--white);
  }
  .services-title { position: absolute; left: 22px; top: 18px; font-weight: 700; font-size: 19px; }
  .services-text { position: absolute; left: 22px; top: 46px; font-size: 15.5px; line-height: 18px; }
  .back-mark {
    position: absolute; left: 382px; top: 106px; width: 216px; height: 216px;
    border-radius: 50%; background: var(--cream);
  }
  .back-mission {
    position: absolute; left: 22px; top: 333px;
    font-family: "Arimo", sans-serif; font-size: 16.5px; color: var(--ink);
  }
</style>
</head>
<body>

<section class="card card-front">
  <div class="front-mark" role="img" aria-label="Jolly Paws emblem area"></div>
  <h1 class="brand-name">JOLLY PAWS</h1>
  <p class="brand-tagline">HAPPY DOGS, HAPPY OWNERS</p>
  <div class="front-band"></div>
  <div class="services-pill">SERVICES</div>
  <p class="front-services-text">Providing individual coaching strategies to create happy,<br>healthy and social canine companions</p>
</section>

<section class="card card-back">
  <h2 class="person-name">Denise Carvell</h2>
  <p class="person-quals">Qualified in Dog Behavioural Training,<br>Natural Animal Healthcare &amp; Animal Health Science</p>

  <div class="contact-band">
    <div class="contact-row row-1">
      <svg viewBox="0 0 14 14" aria-hidden="true"><path d="M3 0h8a1 1 0 0 1 1 1v12a1 1 0 0 1-1 1H3a1 1 0 0 1-1-1V1a1 1 0 0 1 1-1zm1 2v4h6V2zm0 6v1.5h1.5V8zm2.3 0v1.5h1.5V8zm2.3 0v1.5H10V8zM4 10.5V12h1.5v-1.5zm2.3 0V12h1.5v-1.5zm2.3 0V12H10v-1.5z"/></svg>
      <span>0400 172 538</span>
      <span class="spacer"></span>
      <svg viewBox="0 0 14 14" aria-hidden="true"><path d="M0 3h14v1L7 8 0 4zM0 5.5l7 4 7-4V11H0z"/></svg>
      <span>jollypaws1@mailbox.com</span>
    </div>
    <div class="contact-row row-2">
      <svg viewBox="0 0 14 14" aria-hidden="true"><path d="M7 0a7 7 0 1 0 0 14A7 7 0 0 0 7 0zm-1 1.6V4H3.2A5.5 5.5 0 0 1 6 1.6zm2 0A5.5 5.5 0 0 1 10.8 4H8zM2.4 5.5H6v3H2.4a5.5 5.5 0 0 1 0-3zm5.6 0h3.6a5.5 5.5 0 0 1 0 3H8zM3.2 10H6v2.4A5.5 5.5 0 0 1 3.2 10zM8 10h2.8A5.5 5.5 0 0 1 8 12.4z"/></svg>
      <span>www.jollypaws1.com</span>
    </div>
  </div>

  <div class="services-band">
    <h3 class="services-title">SERVICES</h3>
    <p class="services-text">Providing individual coaching strategies to create<br>happy, healthy and social canine companions</p>
  </div>

  <div class="back-mark" role="img" aria-label="Jolly Paws emblem area"></div>

  <p class="back-mission">Promoting communication and connection between dogs and their families</p>
</section>

</body>
</html>
```